Agriculture Business Card

I want to use my existing logo and use my tagline of "Don't Guess...Soil Test" on the card. Looking for a double sided card that will really get peoples attention.
Contact Info:
Marlow Field Crop Edge
Calvin Brusk
2917 K Lane
Larkin, NE 68593
402-555-0193
calvin.r.brusk@fieldmailbox.net

```html
<!DOCTYPE html>
<html lang="en">
<head>
<meta charset="utf-8">
<title>Marlow Field Crop Edge – Business Card</title>
<link href="https://fonts.googleapis.com/css2?family=Montserrat:wght@400;500;600;700&display=swap" rel="stylesheet">
<style>
  :root {
    --field-green: #3cae4a;
    --deep-green: #2f9a3e;
    --harvest-orange: #f4a71d;
    --soil-brown: #9b5f43;
    --ink-grey: #555a5e;
    --paper: #ffffff;
    --backdrop: #e9ebe8;
  }
  * { margin: 0; padding: 0; box-sizing: border-box; }
  html, body { width: 1200px; height: 900px; overflow: hidden; }
  body {
    background: var(--backdrop);
    font-family: "Montserrat", sans-serif;
    position: relative;
  }
  .card {
    position: absolute;
    left: 250px;
    width: 700px;
    height: 400px;
    overflow: hidden;
    box-shadow: 0 10px 30px rgba(0,0,0,0.18);
  }
  .card--front { top: 35px; background: var(--paper); }
  .card--back { top: 465px; background: var(--field-green); }

  .front-wave { position: absolute; inset: 0; width: 100%; height: 100%; }

  .brand {
    position: absolute;
    left: 48px;
    top: 110px;
    width: 250px;
    display: flex;
    align-items: center;
    gap: 14px;
  }
  .brand__dot {
    flex: 0 0 auto;
    width: 44px;
    height: 44px;
    border-radius: 50%;
    background: var(--harvest-orange);
  }
  .brand__name {
    font-weight: 700;
    font-size: 24px;
    line-height: 1.15;
    color: var(--soil-brown);
  }

  .divider {
    position: absolute;
    left: 330px;
    top: 70px;
    width: 1px;
    height: 200px;
    background: var(--soil-brown);
    opacity: 0.7;
  }

  .contact {
    position: absolute;
    left: 362px;
    top: 78px;
    color: var(--ink-grey);
  }
  .contact__name {
    font-weight: 700;
    font-size: 26px;
    letter-spacing: 0.5px;
    color: var(--field-green);
    text-transform: uppercase;
    margin-bottom: 16px;
  }
  .contact__address {
    font-size: 15px;
    line-height: 1.45;
    margin-bottom: 14px;
  }
  .contact__line {
    display: flex;
    align-items: center;
    gap: 8px;
    font-size: 15px;
    line-height: 1.6;
  }
  .contact__icon { width: 14px; height: 14px; flex: 0 0 auto; }

  .back-brand {
    position: absolute;
    left: 0; right: 0;
    top: 120px;
    display: flex;
    justify-content: center;
    align-items: center;
    gap: 16px;
  }
  .back-brand__dot {
    width: 54px; height: 54px; border-radius: 50%;
    background: var(--paper);
  }
  .back-brand__name {
    font-weight: 700;
    font-size: 34px;
    color: var(--paper);
    line-height: 1.1;
  }
  .tagline {
    position: absolute;
    left: 0; right: 0;
    top: 290px;
    text-align: center;
    font-size: 22px;
    font-weight: 500;
    letter-spacing: 1px;
    color: var(--paper);
  }
</style>
</head>
<body>

  <section class="card card--front" aria-label="Card front">
    <svg class="front-wave" viewBox="0 0 700 400" preserveAspectRatio="none" aria-hidden="true">
      <path d="M0 262 C 160 290, 330 375, 470 388 C 560 396, 640 390, 700 382 L700 400 L0 400 Z" fill="var(--field-green)"/>
      <path d="M0 244 C 110 258, 210 300, 300 340" fill="none" stroke="var(--harvest-orange)" stroke-width="5" stroke-linecap="round"/>
      <path d="M440 368 C 540 384, 620 384, 700 372" fill="none" stroke="var(--soil-brown)" stroke-width="5"/>
    </svg>

    <div class="brand">
      <span class="brand__dot"></span>
      <span class="brand__name">Marlow Field<br>Crop Edge</span>
    </div>

    <div class="divider"></div>

    <div class="contact">
      <h1 class="contact__name">Calvin Brusk</h1>
      <p class="contact__address">2917 K Lane<br>Larkin, NE 68593</p>
      <p class="contact__line">
        <svg class="contact__icon" viewBox="0 0 24 24" aria-hidden="true"><path fill="var(--harvest-orange)" d="M6.6 10.8a15 15 0 0 0 6.6 6.6l2.2-2.2a1 1 0 0 1 1-.25 11.4 11.4 0 0 0 3.6.57 1 1 0 0 1 1 1V20a1 1 0 0 1-1 1A17 17 0 0 1 3 4a1 1 0 0 1 1-1h3.5a1 1 0 0 1 1 1c0 1.25.2 2.45.57 3.57a1 1 0 0 1-.25 1z"/></svg>
        402-555-0193
      </p>
      <p class="contact__line">
        <svg class="contact__icon" viewBox="0 0 24 24" aria-hidden="true"><path fill="var(--harvest-orange)" d="M2 5h20v14H2z"/><path fill="none" stroke="#fff" stroke-width="2" d="M2 5l10 8 10-8"/></svg>
        calvin.r.brusk@fieldmailbox.net
      </p>
    </div>
  </section>

  <section class="card card--back" aria-label="Card back">
    <div class="back-brand">
      <span class="back-brand__dot"></span>
      <span class="back-brand__name">Marlow Field<br>Crop Edge</span>
    </div>
    <p class="tagline">Don't Guess...Soil Test</p>
  </section>

</body>
</html>
```